UI/ UX Design for ERP Software

We need a new UX/UI interface for a ERP software for property managers. Our CMMS / ERP solution is made based on responsive design technologies and is coded in PHP.
The overall UX to be similar to Tev Ulna - easy navigation, intuitive menus.

Industry/Entity Type

Property Management

Number of Pages Required

5+ page

Requirements
Must have
• Round dock buttons
Consistent icons across the application
Enough Spacing between buttons/icons/ menu
Consistent Font
Nice to have
• We would like the UX to allow the users to use the application without /minimum training.
Should not have
• we don't want anything that is classic with respect to UX

```html
<!DOCTYPE html>
<html lang="en">
<head>
<meta charset="utf-8">
<title>Tenvo – Active Dashboard</title>
<link href="https://fonts.googleapis.com/css2?family=Roboto:wght@400;500&display=swap" rel="stylesheet">
<style>
  :root {
    --sidebar: #111111;
    --page-bg: #f3f3f3;
    --surface: #ffffff;
    --ink: #111111;
    --muted: #444444;
    --accent: #0d4fa3;
    --icon-bg: #5bc8f5;
    --grid: #c9c9c9;
    --bar: #2f73b7;
    --brand: #1e8fe0;
  }
  * { box-sizing: border-box; margin: 0; padding: 0; }
  html, body { width: 1200px; height: 637px; overflow: hidden; }
  body { position: relative; background: var(--page-bg); font-family: "Roboto", sans-serif; color: var(--ink); }

  .sidebar { position: absolute; left: 0; top: 0; width: 69px; height: 637px; background: var(--sidebar); }
  .sidebar .menu-toggle { position: absolute; left: 19px; top: 22px; }

  .topbar { position: absolute; left: 69px; top: 0; width: 1131px; height: 61px; background: var(--surface); box-shadow: 0 1px 3px rgba(0,0,0,.06); }
  .brand { position: absolute; left: 10px; top: 17px; display: flex; align-items: center; gap: 6px; }
  .brand-mark { width: 22px; height: 22px; background: var(--brand); border-radius: 50%; }
  .brand-name { font-size: 22px; font-weight: 500; color: var(--brand); }
  .page-title { position: absolute; left: 153px; top: 20px; display: flex; align-items: center; gap: 9px; font-size: 17px; }
  .top-actions { position: absolute; left: 904px; top: 16px; display: flex; align-items: center; }
  .top-actions .icon-btn { margin-right: 14px; }
  .avatar { width: 28px; height: 28px; border-radius: 50%; background: linear-gradient(#d9d2cb, #8c7f74); margin-right: 10px; }
  .user-name { font-size: 16px; margin-right: 8px; }

  .stat-card { position: absolute; top: 90px; height: 60px; background: var(--surface); box-shadow: 0 1px 4px rgba(0,0,0,.12); display: flex; align-items: center; padding-left: 14px; }
  .stat-icon { width: 35px; height: 35px; border-radius: 50%; background: var(--icon-bg); display: flex; align-items: center; justify-content: center; margin-right: 10px; flex-shrink: 0; }
  .stat-value { font-size: 16px; font-weight: 500; line-height: 1.2; }
  .stat-label { font-size: 12.5px; line-height: 1.4; }

  .chart-panel { position: absolute; left: 92px; top: 177px; width: 1071px; height: 432px; background: var(--surface); box-shadow: 0 1px 4px rgba(0,0,0,.1); }
  .range-btn { position: absolute; top: 19px; width: 115px; height: 33px; display: flex; align-items: center; justify-content: center; gap: 6px; font-size: 10px; font-weight: 500; background: var(--accent); color: #fff; border: 1px solid var(--accent); }
  .range-btn.is-active { background: var(--surface); color: var(--ink); }
  .date-range { position: absolute; left: 28px; top: 100px; display: flex; align-items: center; gap: 12px; font-size: 12px; }
  .chart { position: absolute; left: 0; top: 0; }
  .chart text { font-family: "Roboto", sans-serif; fill: var(--ink); }
  .legend { position: absolute; left: 66px; top: 364px; width: 1000px; font-size: 10px; }
  .legend-item { position: absolute; display: flex; align-items: center; gap: 7px; white-space: nowrap; }
  .swatch { width: 14px; height: 9px; }
</style>
</head>
<body>
  <aside class="sidebar">
    <svg class="menu-toggle" width="26" height="22" viewBox="0 0 26 22"><rect y="0" width="26" height="3.5" fill="#fff"/><rect y="9" width="26" height="3.5" fill="#fff"/><rect y="18" width="26" height="3.5" fill="#fff"/></svg>
  </aside>

  <header class="topbar">
    <div class="brand"><span class="brand-mark"></span><span class="brand-name">Tenvo</span></div>
    <div class="page-title">
      <svg width="20" height="20" viewBox="0 0 20 20" fill="none" stroke="#333" stroke-width="1.3"><path d="M2 9 10 2l8 7M4 8v10h4v-6h4v6h4V8"/></svg>
      <span>Active Dashboard</span>
    </div>
    <div class="top-actions">
      <svg class="icon-btn" width="22" height="22" viewBox="0 0 22 22" fill="none" stroke="#222" stroke-width="1.8"><circle cx="9" cy="9" r="7"/><path d="M14 14l6 6"/></svg>
      <svg class="icon-btn" width="20" height="22" viewBox="0 0 20 22" fill="none" stroke="#222" stroke-width="1.4"><path d="M4 16V10a6 6 0 0 1 12 0v6l2 2H2z"/><path d="M8 19a2 2 0 0 0 4 0"/><circle cx="15" cy="4" r="2.5"/></svg>
      <div class="avatar" role="img" aria-label="User profile photo"></div>
      <span class="user-name">Dana</span>
      <svg width="9" height="6" viewBox="0 0 9 6" fill="none" stroke="#222" stroke-width="1.3"><path d="M1 1l3.5 3.5L8 1"/></svg>
    </div>
  </header>

  <section class="stat-card" style="left:94px;width:160px;">
    <div class="stat-icon"><svg width="18" height="18" viewBox="0 0 20 20" fill="none" stroke="#1a3550" stroke-width="1.3"><path d="M2 9 10 2l8 7M4 8v10h4v-6h4v6h4V8"/></svg></div>
    <div><div class="stat-value">3</div><div class="stat-label">PROPERTIES</div></div>
  </section>
  <section class="stat-card" style="left:287px;width:160px;">
    <div class="stat-icon"><svg width="18" height="18" viewBox="0 0 20 20" fill="none" stroke="#1a3550" stroke-width="1.3"><circle cx="8" cy="6" r="3.5"/><path d="M2 18c0-4 3-6 6-6s6 2 6 6"/><path d="M12 13l4-3 3 3v5h-7z"/></svg></div>
    <div><div class="stat-value">8</div><div class="stat-label">TENANTS</div></div>
  </section>
  <section class="stat-card" style="left:481px;width:203px;">
    <div class="stat-icon"><svg width="18" height="18" viewBox="0 0 20 20" fill="none" stroke="#1a3550" stroke-width="1.3"><rect x="3" y="3" width="14" height="14"/><path d="M3 7h4M7 3v7M12 12h5"/></svg></div>
    <div><div class="stat-value">422,000.00 SQ.FT.</div><div class="stat-label">TOTAL PROPERTIES AREA</div></div>
  </section>
  <section class="stat-card" style="left:716px;width:203px;">
    <div class="stat-icon"><svg width="18" height="18" viewBox="0 0 20 20" fill="none" stroke="#1a3550" stroke-width="1.3"><path d="M3 17l2-12 5 2 5-3-1 13-5-2z"/><circle cx="9" cy="7" r="1.5"/><circle cx="12" cy="12" r="1.5"/></svg></div>
    <div><div class="stat-value">233,500.00 SQ.FT.</div><div class="stat-label">RENTED AREA</div></div>
  </section>
  <section class="stat-card" style="left:952px;width:203px;">
    <div class="stat-icon"><svg width="18" height="18" viewBox="0 0 20 20" fill="none" stroke="#1a3550" stroke-width="1.3"><circle cx="12" cy="8" r="5"/><path d="M8 12l-6 6"/><circle cx="12" cy="7" r="1.5"/></svg></div>
    <div><div class="stat-value">188,500.00 SQ.FT.</div><div class="stat-label">VACANCIES AREA</div></div>
  </section>

  <main class="chart-panel">
    <div class="range-btn is-active" style="left:300px;"><svg width="10" height="10" viewBox="0 0 10 10" fill="none" stroke="currentColor" stroke-width="1.3"><circle cx="5" cy="5" r="4"/><path d="M5 3v2H3.5"/></svg>LAST 7 DAYS</div>
    <div class="range-btn" style="left:429px;"><svg width="10" height="10" viewBox="0 0 10 10" fill="none" stroke="currentColor" stroke-width="1.3"><circle cx="5" cy="5" r="4"/><path d="M5 3v2H3.5"/></svg>LAST MONTHS</div>
    <div class="range-btn" style="left:557px;"><svg width="10" height="10" viewBox="0 0 10 10" fill="none" stroke="currentColor" stroke-width="1.3"><circle cx="5" cy="5" r="4"/><path d="M5 3v2H3.5"/></svg>LAST 3 MONTHS</div>
    <div class="range-btn" style="left:684px;"><svg width="10" height="10" viewBox="0 0 10 10" fill="none" stroke="currentColor" stroke-width="1.3"><circle cx="5" cy="5" r="4"/><path d="M5 3v2H3.5"/></svg>NEXT 3 DAYS</div>
    <div class="range-btn" style="left:813px;"><svg width="10" height="10" viewBox="0 0 10 10" fill="none" stroke="currentColor" stroke-width="1.3"><circle cx="5" cy="5" r="4"/><path d="M5 3v2H3.5"/></svg>NEXT MONTH</div>
    <div class="range-btn" style="left:941px;"><svg width="10" height="10" viewBox="0 0 10 10" fill="none" stroke="currentColor" stroke-width="1.3"><circle cx="5" cy="5" r="4"/><path d="M5 3v2H3.5"/></svg>NEXT 3 MONTHS</div>

    <div class="date-range">
      <svg width="14" height="14" viewBox="0 0 14 14" fill="none" stroke="#222" stroke-width="1.1"><rect x="1" y="2.5" width="12" height="10.5"/><path d="M1 5.5h12M4 1v3M10 1v3M4.5 5.5v7.5M7 5.5v7.5M9.5 5.5v7.5M1 8h12M1 10.5h12"/></svg>
      <span>12/27/2020 &nbsp;-&nbsp; 01/03/2021</span>
    </div>

    <svg class="chart" width="1071" height="360" viewBox="0 0 1071 360">
      <g fill="#111"><rect x="22" y="139" width="14" height="1.8"/><rect x="22" y="142.5" width="14" height="1.8"/><rect x="22" y="146" width="14" height="1.8"/><rect x="22" y="149.5" width="14" height="1.8"/></g>
      <g stroke="var(--grid)" stroke-width="0.8">
        <line x1="77" y1="144" x2="1054" y2="144"/><line x1="77" y1="181" x2="1054" y2="181"/>
        <line x1="77" y1="217" x2="1054" y2="217"/><line x1="77" y1="253" x2="1054" y2="253"/>
        <line x1="77" y1="289" x2="1054" y2="289"/><line x1="77" y1="325" x2="1054" y2="325"/>
      </g>
      <g font-size="9">
        <text x="48" y="147">1.25</text><text x="48" y="184">1</text><text x="48" y="220">0.75</text>
        <text x="48" y="256">0.5</text><text x="48" y="292">0.25</text><text x="48" y="328">0</text>
      </g>
      <text font-size="10.5" transform="translate(31 238) rotate(-90)" text-anchor="middle">Numbers</text>
      <rect x="468" y="181" width="6" height="144" fill="var(--bar)"/>
      <g font-size="9" text-anchor="middle">
        <text x="140" y="342">12/27/2020</text><text x="262" y="342">12/28/2020</text>
        <text x="385" y="342">12/29/2020</text><text x="507" y="342">12/30/2020</text>
        <text x="629" y="342">12/31/2020</text><text x="751" y="342">01/01/2020</text>
        <text x="873" y="342">01/02/2020</text><text x="996" y="342">01/03/2020</text>
      </g>
    </svg>

    <div class="legend">
      <div class="legend-item" style="left:0;top:0;"><span class="swatch" style="background:#2f73b7"></span>Scheduled Maintenance</div>
      <div class="legend-item" style="left:142px;top:0;"><span class="swatch" style="background:#8de27a"></span>Completed Scheduled Maintenance</div>
      <div class="legend-item" style="left:342px;top:0;"><span class="swatch" style="background:#f4a35c"></span>Future Scheduled Maintenance</div>
      <div class="legend-item" style="left:521px;top:0;"><span class="swatch" style="background:#3d3f45"></span>Scheduled Work Orders</div>
      <div class="legend-item" style="left:668px;top:0;"><span class="swatch" style="background:#8a8ff0"></span>Completed Work Orders</div>
      <div class="legend-item" style="left:820px;top:0;"><span class="swatch" style="background:#ef5a7e"></span>Property Inspections in Progress</div>
      <div class="legend-item" style="left:0;top:24px;"><span class="swatch" style="background:#e6d65a"></span>Completed Property Inspections</div>
    </div>
  </main>
</body>
</html>
```